BOLD & MINIMALIST DESIGN NEEDED

We want a very bold but minimalistic business card design that is impactful and utilizes both sides of the business card. Our current logo is included for your use.

We want bold fonts and good use of negative space. We don't want the logo to overpower the design.

Target Market(s)

Professionals who are building new commercial buildings.

Industry/Entity Type

Construction

Contact Information for Business Card

Name, Title, email, office phone, cell phone, website

Font styles to use
Serif
Sans Serif

Requirements
Must have
• Bold design!

```html
<!DOCTYPE html>
<html lang="en">
<head>
<meta charset="utf-8">
<title>Varnholt Business Card</title>
<link rel="stylesheet" href="https://fonts.googleapis.com/css2?family=Arimo:wght@400;700&display=swap">
<style>
  :root {
    --page: #e4e4e4;
    --paper: #f3f3f3;
    --ink: #0b0b0b;
    --white: #ffffff;
    --green: #7dba27;
    --green-light: #a9d46c;
    --green-deep: #7bb821;
  }
  html, body {
    margin: 0;
    padding: 0;
    width: 1200px;
    height: 1040px;
    overflow: hidden;
    background: var(--page);
    font-family: "Arimo", Arial, sans-serif;
  }
  .canvas {
    position: relative;
    width: 1200px;
    height: 1040px;
  }
  .card {
    position: absolute;
    left: 285px;
    width: 640px;
    height: 366px;
    border-radius: 18px;
    overflow: hidden;
  }
  .card--front { top: 130px; background: var(--paper); }
  .card--back {
    top: 568px;
    left: 284px;
    width: 646px;
    height: 368px;
    background: radial-gradient(ellipse at 50% 45%, var(--green-light) 0%, #98cb4f 40%, var(--green-deep) 100%);
  }
  .front-shapes {
    position: absolute;
    inset: 0;
    width: 640px;
    height: 366px;
  }
  .brand {
    position: absolute;
    display: flex;
    align-items: center;
    justify-content: center;
    color: var(--ink);
    font-weight: 700;
    letter-spacing: 0.5px;
    white-space: nowrap;
  }
  .brand__mark { background: var(--green); flex: none; }
  .brand--front {
    left: 20px;
    width: 278px;
    top: 98px;
    height: 44px;
    font-size: 34px;
    gap: 10px;
  }
  .brand--front .brand__mark { width: 22px; height: 22px; }
  .brand--back {
    left: 0; right: 0; top: 150px;
    height: 70px;
    font-size: 60px;
    gap: 16px;
  }
  .brand--back .brand__mark { width: 38px; height: 38px; background: var(--ink); }
  .contact {
    position: absolute;
    right: 41px;
    top: 164px;
    text-align: right;
    color: var(--white);
  }
  .contact__name {
    margin: 0;
    color: var(--green);
    font-size: 25px;
    font-weight: 700;
    line-height: 1.1;
  }
  .contact__title { margin: 2px 0 0; font-size: 16px; }
  .contact__address { margin: 12px 0 0; padding-right: 1px; font-size: 16px; line-height: 20px; }
  .contact__lines { list-style: none; margin: 11px 0 0; padding: 0; font-size: 16px; }
  .contact__lines li {
    display: flex;
    justify-content: flex-end;
    align-items: center;
    gap: 10px;
    height: 20px;
  }
  .contact__icon { width: 13px; height: 13px; fill: var(--green); flex: none; }
</style>
</head>
<body>
<main class="canvas">
  <section class="card card--front" aria-label="Card front">
    <svg class="front-shapes" viewBox="0 0 640 366" aria-hidden="true">
      <polygon points="498,0 640,0 640,366 238,366" fill="var(--ink)"/>
      <polygon points="489,0 495,0 215,366 191,366" fill="var(--green)"/>
    </svg>
    <div class="brand brand--front"><span class="brand__mark"></span>VARNHOLT</div>
    <div class="contact">
      <p class="contact__name">JONAH REYES</p>
      <p class="contact__title">President</p>
      <p class="contact__address">2710 Alder Court<br>Millbrook, NY 12545</p>
      <ul class="contact__lines">
        <li>(555) 0142-7788
          <svg class="contact__icon" viewBox="0 0 16 16"><path d="M3 1l3 0 1 4-2 1c1 2 3 4 5 5l1-2 4 1 0 3c0 1-1 2-2 2C7 15 1 9 1 3c0-1 1-2 2-2z"/></svg>
        </li>
        <li>info@varnholt.com
          <svg class="contact__icon" viewBox="0 0 16 16"><path d="M1 3h14v10H1z M1 3l7 6 7-6" stroke="var(--ink)" stroke-width="1"/></svg>
        </li>
        <li>www.varnholt.com
          <svg class="contact__icon" viewBox="0 0 16 16"><circle cx="8" cy="8" r="7"/><path d="M1 8h14M8 1c-3 4-3 10 0 14M8 1c3 4 3 10 0 14" stroke="var(--ink)" stroke-width="1" fill="none"/></svg>
        </li>
      </ul>
    </div>
  </section>

  <section class="card card--back" aria-label="Card back">
    <div class="brand brand--back"><span class="brand__mark"></span>VARNHOLT</div>
  </section>
</main>
</body>
</html>
```